New Business Card Design Project

We require a business card design for Vexalund, a newly established Indian company.
Our focus is on the development, manufacturing, and export of a diverse array of pharmaceutical products on a global scale. The card should convey a professional appearance, as our primary markets are in Africa, China, and Southeast Asian nations.
We envision a two-sided business card, with the reverse side dedicated to a logo set against a solid color or an elegantly designed pattern. The corners should be rounded. We would appreciate seeing both horizontal and vertical design options. We trust the designer to utilize their expertise in creating this design.

The content for the business card is included in the attached Word file.

Target Market(s)

Our primary markets are in Africa, China, and Southeast Asian, Latin America, Maldives, Sri Lanka

Industry/Entity Type

Pharmaceutical Manufacturing and Export

Contact Information for Business Card

Colors

Designer to choose colors to be used in the design.

Requirements
Must have
• The reverse side of the business card features solely the logo along with the tagline, "Care Across Borders."
Should not have
• The logo should not exceed two instances, encompassing both the front and back sides of the card.

```html
<!DOCTYPE html>
<html lang="en">
<head>
<meta charset="utf-8">
<title>Vexalund Business Card</title>
<link rel="stylesheet" href="https://fonts.googleapis.com/css2?family=Montserrat:wght@500;700;800&family=Open+Sans:wght@400;600&display=swap">
<style>
  :root {
    --stage: #222224;
    --card-dark: #1f1f22;
    --brand-blue: #2fa8e0;
    --brand-blue-deep: #1b8ccc;
    --accent-coral: #f0614b;
    --text-light: #f2f2f2;
    --text-soft: #e6e6e6;
  }
  * { box-sizing: border-box; margin: 0; padding: 0; }
  html, body {
    width: 1200px; height: 711px; overflow: hidden;
    background: var(--stage);
  }
  .stage {
    position: relative; width: 1200px; height: 711px;
    display: flex; align-items: center; justify-content: center; gap: 50px;
  }
  .card {
    position: relative; width: 525px; height: 300px;
    border-radius: 24px; overflow: hidden;
  }
  /* Back side */
  .card-back {
    background: var(--brand-blue);
    display: flex; flex-direction: column; align-items: center; justify-content: center;
  }
  .back-wordmark {
    font-family: 'Montserrat', sans-serif; font-weight: 800;
    font-size: 64px; letter-spacing: 1px; color: var(--brand-blue-deep);
  }
  .back-tagline {
    margin-top: 10px;
    font-family: 'Montserrat', sans-serif; font-weight: 500;
    font-size: 15px; letter-spacing: 0.5px; color: #ffffff;
  }
  /* Front side */
  .card-front {
    background: var(--card-dark);
    border-bottom: 4px solid var(--brand-blue);
  }
  .corner-bar {
    position: absolute; top: 0; right: 0; width: 14px; height: 66px;
    background: var(--brand-blue);
  }
  .holder {
    position: absolute; top: 24px; right: 34px; text-align: right;
  }
  .holder-name {
    font-family: 'Montserrat', sans-serif; font-size: 24px; line-height: 1.1;
  }
  .holder-first { font-weight: 700; color: var(--brand-blue); }
  .holder-last { font-weight: 500; color: var(--accent-coral); }
  .holder-role {
    margin-top: 4px;
    font-family: 'Open Sans', sans-serif; font-size: 13px; color: var(--text-light);
  }
  .front-wordmark {
    position: absolute; left: 34px; top: 112px;
    font-family: 'Montserrat', sans-serif; font-weight: 800;
    font-size: 44px; color: var(--brand-blue);
  }
  .address {
    position: absolute; left: 36px; top: 178px;
    font-family: 'Open Sans', sans-serif; font-style: normal;
    font-size: 12.5px; line-height: 1.45; color: var(--text-soft);
  }
  .contacts {
    position: absolute; left: 36px; top: 222px; list-style: none;
    font-family: 'Open Sans', sans-serif; font-size: 12.5px; color: var(--text-soft);
  }
  .contacts li { display: flex; align-items: center; gap: 10px; height: 20px; }
  .contacts svg { width: 14px; height: 14px; flex: none; }
</style>
</head>
<body>
<main class="stage">
  <section class="card card-back" aria-label="Card reverse">
    <div class="back-wordmark">Vexalund</div>
    <div class="back-tagline">Care Across Borders.</div>
  </section>

  <section class="card card-front" aria-label="Card front">
    <span class="corner-bar"></span>
    <div class="holder">
      <div class="holder-name"><span class="holder-first">Rohan</span> <span class="holder-last">K. Malvade</span></div>
      <div class="holder-role">CEO</div>
    </div>

    <div class="front-wordmark">Vexalund</div>

    <address class="address">
      14, Sarovar Nagar,<br>Nashik, 422005, India
    </address>

    <ul class="contacts">
      <li>
        <svg viewBox="0 0 14 14" aria-hidden="true"><rect x="3" y="1" width="8" height="12" rx="1.5" fill="none" stroke="var(--accent-coral)" stroke-width="1.5"/></svg>
        +91 98765 43210
      </li>
      <li>
        <svg viewBox="0 0 14 14" aria-hidden="true"><circle cx="7" cy="7" r="6" fill="var(--brand-blue)"/><path d="M1 7h12M7 1c-3 3-3 9 0 12M7 1c3 3 3 9 0 12" fill="none" stroke="#fff" stroke-width="0.8"/></svg>
        www.vexalund.com
      </li>
      <li>
        <svg viewBox="0 0 14 14" aria-hidden="true"><rect x="1" y="3" width="12" height="9" rx="1" fill="var(--accent-coral)"/><path d="M1.5 3.5 7 8l5.5-4.5" fill="none" stroke="#fff" stroke-width="1"/></svg>
        rmalvade@vexalund.com
      </li>
    </ul>
  </section>
</main>
</body>
</html>
```